Business Card for Vorla Parts Wholesale supplier

Hi There! I need a new business card for our company. We are specialized in selling Vorla parts, mostly we sell new LCD screens for Zelnar and Drelks. I would like to see that back in the design.

You can find the colors and logo's on our website: www.hartuvo.nl

Industry/Entity Type

Business

Contact Information for Business Card

My Details:
Tobias Lindqvist

Phone: 0031687203316
E-mail: Tobias@hartuvo.nl

Slogan: "Because Quality Matters"

Font styles to use
Sans Serif

Colors

Designer to choose colors to be used in the design.

Requirements
Must have
• A Black backside with the Hartuvo logo on it. The front side should be clean with only my contact details.
• But I'm also open for something really different or awesome!
Nice to have
• Remember that we are in the parts & repairing industry, So i'll be handing those business cards mainly to repair companies. Maybe you can do something with that thought :)

```html
<!DOCTYPE html>
<html lang="en">
<head>
<meta charset="UTF-8">
<title>Hartuvo Business Card</title>
<link href="https://fonts.googleapis.com/css2?family=Open+Sans:ital,wght@0,400;0,700;0,800;1,400&display=swap" rel="stylesheet">
<style>
  :root {
    --backdrop: #e6e6e6;
    --card-white: #ffffff;
    --brand-orange: #f07522;
    --brand-orange-light: #f48a3c;
    --ink: #141414;
    --card-black: #0d0d0d;
    --card-black-soft: #262626;
    --on-dark: #ffffff;
  }
  * { margin: 0; padding: 0; box-sizing: border-box; }
  html, body {
    width: 1200px;
    height: 950px;
    overflow: hidden;
    background: var(--backdrop);
    font-family: "Open Sans", Arial, sans-serif;
  }
  .sheet {
    width: 1200px;
    height: 950px;
    display: flex;
    flex-direction: column;
    align-items: center;
    justify-content: center;
    gap: 40px;
  }
  .card {
    width: 640px;
    height: 414px;
    position: relative;
    overflow: hidden;
    box-shadow: 0 10px 30px rgba(0,0,0,0.18);
  }

  /* Front side */
  .card-front {
    background: var(--card-white);
    display: flex;
    flex-direction: column;
  }
  .front-brand {
    flex: 1;
    display: flex;
    align-items: center;
    justify-content: center;
  }
  .brand-lockup {
    display: flex;
    align-items: center;
    gap: 16px;
  }
  .brand-dot {
    width: 58px;
    height: 58px;
    border-radius: 50%;
    background: var(--brand-orange);
  }
  .brand-name {
    font-weight: 800;
    font-size: 74px;
    line-height: 1;
    letter-spacing: -1px;
    color: var(--ink);
  }
  .contact-band {
    height: 124px;
    background: linear-gradient(90deg, var(--brand-orange-light), var(--brand-orange));
    color: var(--on-dark);
    display: flex;
    flex-direction: column;
    align-items: center;
    justify-content: center;
    gap: 6px;
  }
  .contact-name {
    font-weight: 700;
    font-size: 26px;
  }
  .contact-line {
    font-weight: 400;
    font-size: 17px;
    letter-spacing: 0.2px;
  }
  .contact-line .sep { margin: 0 6px; }

  /* Back side */
  .card-back {
    background: linear-gradient(135deg, var(--card-black) 0%, var(--card-black-soft) 45%, var(--card-black) 100%);
    display: flex;
    flex-direction: column;
    align-items: center;
    justify-content: center;
    gap: 18px;
  }
  .card-back .brand-name { color: var(--on-dark); }
  .slogan {
    font-style: italic;
    font-size: 18px;
    color: var(--brand-orange);
    letter-spacing: 0.5px;
    margin-left: 74px;
  }
</style>
</head>
<body>
  <main class="sheet">
    <section class="card card-front" aria-label="Business card front">
      <div class="front-brand">
        <div class="brand-lockup">
          <span class="brand-dot"></span>
          <span class="brand-name">hartuvo</span>
        </div>
      </div>
      <div class="contact-band">
        <p class="contact-name">Tobias Lindqvist</p>
        <p class="contact-line">0031687203316<span class="sep">|</span>Tobias@hartuvo.nl<span class="sep">|</span>www.hartuvo.nl</p>
      </div>
    </section>

    <section class="card card-back" aria-label="Business card back">
      <div class="brand-lockup">
        <span class="brand-dot"></span>
        <span class="brand-name">hartuvo</span>
      </div>
      <p class="slogan">Because Quality Matters</p>
    </section>
  </main>
</body>
</html>
```